Brivora Distance Learning Website

Brivora provide e-learning and mixed learning solutions for individuals, colleges, organisations and B2B.
We need a modern, light and flat website design for Brivora. We want to to see the designer incorporate user experience(UX) design elements into the AI or PSD mockups. We would like to see designs that use pastel colors that compliment yellow and black of our logo.
We want our E-learning experience to accelerate learning and for the interface to be user friendly and intuitive. We want the designs to focus on quick access to course information, course reviews, learning progress and study advice. Quick and intuitive access to all content for our clients is one of our top priorities.
We would like designs for the following project 3 pages:
1. Learner homepage dashboard (see attached screenshot).
On this page the Learners need to:
- Login
- Have quick access to Packages and Courses.
- See other recommended courses (Below Packages and Courses)
- Possibly a left hand side column/menu with thumbnail icons (See lumeqa learner dashboard screenshot)
2. Homepage
See current sample
http://www.brivora-learn.example
We would like the designer to focus on creating a customized banner to enhance the home page.
3. Primary Landing/Marketing page
This page is geared towards customer acquisition with the focal point being the top banner (video or HD image).
And Course Preview content below.
See reference
http://brivora-learn.example/subscriptionPlans/marketing/MTc%3D/Mjc4Nw%3D%3D/Speaking%20Nepali%20%2B%20Nepali%20Snacks%20Bundle%20by%20Lorne%20Pike%20Vell
Other site we like:
- https://www.skillorva.example (We like the home page and top bar on courses page)
- http://www.tutorcrest.example
- http://pixelgrovelab.example (think this site looks great, love the lower graphics on the homepage)
Updates
Hello,
Thank you for taking the time to contribute to this web design competition. We would just like to point out a few things:
1. Please try to make the color palette similar to the colors used in the screenshot that we just uploaded ('possible color palette).
2. Please make the designs specific to each page: THE LEARNER HOMEPAGE, HOME PAGE, and the MARKETING LANDING PAGE.
We are very happy with the high quality of designs so far,
Cheers,
Ned Ru
VK-Studio
Also,
Please avoid using dark/bold elements in the designs. The ONLY elements that we want to be dark are the logo and the footer.
Any questions please ask,
Cheers,
Ned Ru
Vk-Studio
Hello,
Based on the round of feedback we just gave it would be great if you could complete further design changes by tomorrow, as we are pushed for time.
Thank you,
Ned Ru
VK-Studio

```html
<!DOCTYPE html>
<html lang="en">
<head>
<meta charset="utf-8">
<title>Brivora – Your Learning Journey Starts Here</title>
<link href="https://fonts.googleapis.com/css2?family=Raleway:wght@400;500;800&family=Roboto:wght@400;500;700&display=swap" rel="stylesheet">
<style>
:root{
  --yellow:#f7b924;
  --yellow-deep:#f2a900;
  --green:#14911e;
  --ink:#222;
  --text:#333;
  --muted:#666;
  --line:#d8d8d8;
  --panel:#f4f4f4;
  --page:#f7f7f7;
  --footer:#3a3a3a;
  --orange:#f4a21c;
  --grey-btn:#dedede;
}
*{box-sizing:border-box;margin:0;padding:0}
html,body{width:961px;height:1200px;overflow:hidden}
body{position:relative;background:var(--page);font-family:"Roboto",Arial,sans-serif;color:var(--text)}
.abs{position:absolute}

/* header */
.site-header{left:0;top:0;width:961px;height:74px;background:#fff;border-bottom:1px solid #e2e2e2}
.brand{display:flex;align-items:center;gap:8px;font-family:"Raleway",sans-serif;font-weight:500;font-size:30px;color:var(--ink);letter-spacing:-.5px}
.brand-dot{width:14px;height:14px;border-radius:50%;background:var(--yellow)}
.site-header .brand{left:84px;top:18px}
.btn-lang,.btn-sign{top:24px;height:26px;font-size:12px;display:flex;align-items:center;justify-content:center;border-radius:2px;color:var(--ink)}
.btn-lang{left:690px;width:84px;background:var(--yellow)}
.btn-sign{left:798px;width:70px;background:var(--grey-btn)}

/* hero */
.hero{left:0;top:74px;width:961px;height:526px;background:linear-gradient(100deg,#7a5b46 0%,#b38a6a 22%,#a9a7a6 45%,#c9bfb4 65%,#e8e1da 82%,#cfc5bb 100%)}
.hero-shade{left:0;top:74px;width:961px;height:526px;background:rgba(40,30,25,.18)}
.hero-title{left:0;top:144px;width:945px;text-align:center;font-family:"Raleway",sans-serif;font-weight:800;font-size:35px;color:#fff;letter-spacing:-.6px;text-shadow:0 1px 3px rgba(0,0,0,.3)}
.hero-sub{left:0;top:203px;width:945px;text-align:center;font-family:"Raleway",sans-serif;font-size:18px;color:#fff}
.beta-card{left:297px;top:257px;width:366px;height:237px;background:rgba(247,185,36,.95);border-radius:4px}
.beta-title{left:0;top:20px;width:100%;text-align:center;font-family:"Raleway",sans-serif;font-weight:500;font-size:18px;color:var(--ink)}
.field{background:#eee;border:1px solid #c9c9c9;font-size:10px;color:#666;padding:9px 8px}
.field-email{left:50px;top:56px;width:266px;height:27px;padding-top:7px}
.field-reason{left:50px;top:100px;width:266px;height:63px}
.btn-join{left:211px;top:183px;width:105px;height:33px;background:var(--green);color:#fff;font-size:14px;display:flex;align-items:center;justify-content:center;border-radius:2px}
.search-band{left:0;top:518px;width:961px;height:82px;background:rgba(30,40,60,.55)}
.search-input{left:171px;top:542px;width:496px;height:35px;background:#fff;font-size:12px;color:#555;padding:0 14px;display:flex;align-items:center}
.search-btn{left:667px;top:542px;width:107px;height:35px;background:var(--yellow);font-size:18px;color:var(--ink);display:flex;align-items:center;justify-content:center}

/* packages */
.section-title{left:79px;top:630px;width:800px;height:40px;display:flex;align-items:center;gap:4px;font-family:"Raleway",sans-serif;font-size:32px;color:#333}
.section-title::before,.section-title::after{content:"";flex:1;height:1px;background:#999}

.categories{left:79px;top:698px;width:189px;height:392px;background:#fff;box-shadow:0 1px 3px rgba(0,0,0,.2)}
.categories h2{height:41px;background:var(--yellow);font-family:"Roboto",sans-serif;font-weight:400;font-size:19px;color:var(--ink);padding:9px 11px}
.categories ul{list-style:none;padding-top:5px}
.categories li{height:33.8px;border-bottom:1px solid #e4e4e4;font-size:11.5px;color:#222;display:flex;align-items:center;padding-left:20px;position:relative}
.categories li:last-child{border-bottom:none}
.categories li::before{content:"";position:absolute;left:11px;top:50%;width:3px;height:3px;margin-top:-1px;background:#555;border-radius:50%}

.card{top:697px;width:178px;height:323px;background:#fff;border:1px solid #cfcfcf;border-radius:3px;box-shadow:0 1px 3px rgba(0,0,0,.15)}
.card-cover{left:9px;top:9px;width:158px;height:136px;background:linear-gradient(160deg,#f9c42a,#f2ad12)}
.card-meta{left:0;top:153px;width:100%;height:35px;background:var(--panel);border-top:1px solid #ccc;border-bottom:1px solid #ccc;display:flex}
.meta-cat{width:86px;border-right:1px solid #ccc;font-size:10.5px;line-height:12px;padding:6px 0 0 17px;color:#222}
.meta-views{flex:1;display:flex;flex-direction:column;align-items:center;justify-content:center;font-size:11.5px;font-weight:500;color:#222}
.card-body{left:0;top:188px;width:100%;height:135px;background:#f5f5f5}
.reviews{left:0;top:8px;width:100%;text-align:center;font-size:11px;color:#222}
.stars{left:0;top:22px;width:100%;display:flex;justify-content:center;gap:1px}
.card-title{left:14px;top:38px;width:155px;font-size:10.5px;line-height:13px;color:#222}
.card-by{left:14px;top:66px;font-size:10px;color:#222}
.card-by span{font-size:8.5px;color:#666}
.btn-details{left:12px;top:108px;width:150px;height:27px;background:linear-gradient(#8a8a8a,#6a6a6a);color:#fff;font-size:9.5px;font-weight:500;letter-spacing:.4px;display:flex;align-items:center;justify-content:center;gap:6px;border-radius:3px}

.org-title{left:298px;top:1040px;font-family:"Raleway",sans-serif;font-weight:500;font-size:15px;color:var(--orange)}
.org-text{left:298px;top:1062px;width:570px;font-size:10.4px;line-height:16px;color:#222}

/* footer */
.site-footer{left:0;top:1130px;width:961px;height:70px;background:var(--footer)}
.footer-links{left:87px;top:14px;font-size:11px;line-height:16px;color:#ddd}
.site-footer .brand{left:750px;top:16px;color:#fff;font-size:28px}
</style>
</head>
<body>

<header class="site-header abs">
  <div class="brand abs"><span class="brand-dot"></span>Brivora</div>
  <div class="btn-lang abs">English(US)</div>
  <div class="btn-sign abs">Sign In</div>
</header>

<section>
  <div class="hero abs" role="img" aria-label="Blurred city street with a smiling student holding a green folder and giving a thumbs up"></div>
  <div class="hero-shade abs"></div>
  <h1 class="hero-title abs">YOUR LEARNING JOURNEY STARTS HERE</h1>
  <p class="hero-sub abs">facilitating elegant e-learning and mixed learning solutions</p>

  <form class="beta-card abs">
    <h2 class="beta-title abs">Join Our Beta Limited Availability</h2>
    <div class="field field-email abs">Email Address</div>
    <div class="field field-reason abs">Reason for Interest</div>
    <div class="btn-join abs">Join Beta</div>
  </form>

  <div class="search-band abs"></div>
  <div class="search-input abs">What Can We Help You Learn Today?</div>
  <div class="search-btn abs">Search</div>
</section>

<main>
  <h2 class="section-title abs">Learning Packages</h2>

  <nav class="categories abs">
    <h2>Categories</h2>
    <ul>
      <li>Business and Finance</li>
      <li>Marketing</li>
      <li>IT &amp; Software</li>
      <li>Lifestyle</li>
      <li>Personal Development</li>
      <li>Photography</li>
      <li>Health and Fitness</li>
      <li>Education and Teaching</li>
      <li>Music</li>
      <li>Hotels and Hospitality</li>
    </ul>
  </nav>

  <article class="card abs" style="left:297px">
    <div class="card-cover abs" role="img" aria-label="Nepali Snacks course cover artwork"></div>
    <div class="card-meta abs">
      <div class="meta-cat">Language<br>and...</div>
      <div class="meta-views"><svg width="12" height="8" viewBox="0 0 12 8"><ellipse cx="6" cy="4" rx="5.5" ry="3.5" fill="none" stroke="#444" stroke-width="1.2"/><circle cx="6" cy="4" r="1.6" fill="#444"/></svg>Views 1417</div>
    </div>
    <div class="card-body abs">
      <div class="reviews abs">Reviews</div>
      <div class="stars abs">
        <svg width="66" height="12" viewBox="0 0 66 12"><g fill="#f7b924" stroke="#c88a00" stroke-width=".6"><path id="s1" d="M6 .6l1.6 3.4 3.7.4-2.8 2.5.8 3.7L6 8.7 2.7 10.6l.8-3.7L.7 4.4l3.7-.4z"/><use href="#s1" x="13"/><use href="#s1" x="26"/><use href="#s1" x="39"/></g><use href="#s1" x="52" fill="#aaa" stroke="#888"/></svg>
      </div>
      <div class="card-title abs">Speaking Nepali Fundamentals Suite by Lorne Pike Vell</div>
      <div class="card-by abs">by <span>Lorne Vell</span></div>
      <div class="btn-details abs"><svg width="18" height="7" viewBox="0 0 18 7"><rect width="6" height="7" fill="#fff"/><rect x="8" y="0" width="10" height="1.4" fill="#fff"/><rect x="8" y="2.8" width="10" height="1.4" fill="#fff"/><rect x="8" y="5.6" width="10" height="1.4" fill="#fff"/></svg>DETAILS</div>
    </div>
  </article>

  <article class="card abs" style="left:499px">
    <div class="card-cover abs" role="img" aria-label="Nepali Snacks course cover artwork"></div>
    <div class="card-meta abs">
      <div class="meta-cat">Language<br>and...</div>
      <div class="meta-views"><svg width="12" height="8" viewBox="0 0 12 8"><ellipse cx="6" cy="4" rx="5.5" ry="3.5" fill="none" stroke="#444" stroke-width="1.2"/><circle cx="6" cy="4" r="1.6" fill="#444"/></svg>Views 1417</div>
    </div>
    <div class="card-body abs">
      <div class="reviews abs">Reviews</div>
      <div class="stars abs">
        <svg width="66" height="12" viewBox="0 0 66 12"><g fill="#f7b924" stroke="#c88a00" stroke-width=".6"><path id="s2" d="M6 .6l1.6 3.4 3.7.4-2.8 2.5.8 3.7L6 8.7 2.7 10.6l.8-3.7L.7 4.4l3.7-.4z"/><use href="#s2" x="13"/><use href="#s2" x="26"/><use href="#s2" x="39"/></g><use href="#s2" x="52" fill="#aaa" stroke="#888"/></svg>
      </div>
      <div class="card-title abs">Speaking Nepali Fundamentals Suite by Lorne Pike Vell</div>
      <div class="card-by abs">by <span>Lorne Vell</span></div>
      <div class="btn-details abs"><svg width="18" height="7" viewBox="0 0 18 7"><rect width="6" height="7" fill="#fff"/><rect x="8" y="0" width="10" height="1.4" fill="#fff"/><rect x="8" y="2.8" width="10" height="1.4" fill="#fff"/><rect x="8" y="5.6" width="10" height="1.4" fill="#fff"/></svg>DETAILS</div>
    </div>
  </article>

  <article class="card abs" style="left:702px">
    <div class="card-cover abs" role="img" aria-label="Nepali Snacks course cover artwork"></div>
    <div class="card-meta abs">
      <div class="meta-cat">Language<br>and...</div>
      <div class="meta-views"><svg width="12" height="8" viewBox="0 0 12 8"><ellipse cx="6" cy="4" rx="5.5" ry="3.5" fill="none" stroke="#444" stroke-width="1.2"/><circle cx="6" cy="4" r="1.6" fill="#444"/></svg>Views 1417</div>
    </div>
    <div class="card-body abs">
      <div class="reviews abs">Reviews</div>
      <div class="stars abs">
        <svg width="66" height="12" viewBox="0 0 66 12"><g fill="#f7b924" stroke="#c88a00" stroke-width=".6"><path id="s3" d="M6 .6l1.6 3.4 3.7.4-2.8 2.5.8 3.7L6 8.7 2.7 10.6l.8-3.7L.7 4.4l3.7-.4z"/><use href="#s3" x="13"/><use href="#s3" x="26"/><use href="#s3" x="39"/></g><use href="#s3" x="52" fill="#aaa" stroke="#888"/></svg>
      </div>
      <div class="card-title abs">Speaking Nepali Fundamentals Suite by Lorne Pike Vell</div>
      <div class="card-by abs">by <span>Lorne Vell</span></div>
      <div class="btn-details abs"><svg width="18" height="7" viewBox="0 0 18 7"><rect width="6" height="7" fill="#fff"/><rect x="8" y="0" width="10" height="1.4" fill="#fff"/><rect x="8" y="2.8" width="10" height="1.4" fill="#fff"/><rect x="8" y="5.6" width="10" height="1.4" fill="#fff"/></svg>DETAILS</div>
    </div>
  </article>

  <h3 class="org-title abs">Learning for Organisations and Educational Institutions.</h3>
  <p class="org-text abs">Launching Soon! - Brivora will be launching services to integrate Brivora's learning platform into Organisations and Learning Institutes to support Online, Interactive and Blended Learning.</p>
</main>

<footer class="site-footer abs">
  <div class="footer-links abs">Copyright © 2015 Brivora-learn.example<br>Terms of Use<br>Privacy Policy</div>
  <div class="brand abs"><span class="brand-dot"></span>Brivora</div>
</footer>

</body>
</html>
```